CrestHornSupply.com

I need a new webdesign for a company in the San Jose/SF Bay area that showcases the financial benefits of buying used band instruments for junior high students.This would be opposed to the current and costly option of renting cheap quality instruments from the 2 or 3 local music stores that charge a monthly fee that over the years charges the buyer 3 or 4x over..
Instruments: focus in on Alto Sax, Trumpet, Flute, Clarinet, Trombone, Tenor Sax, Baritone
Target middle schools are Larkfield Middle School and Maple Middle School in San Jose, CA. Both have award winning band programs.
Files attached may or may not be important.
Tabs Needed and funtional
Contact
Shopping Cart
Select Instrument
Checkout
Add to Cart, etc.
Instuments
quantity, etc.
trade in your instrument/sell your instrument
ability to add or take away new instruments for sale. including pictures
Additional questions or info, feel free to ask
Updates
Hi Designers,
Project Deadline Extended
Reason: In the next week you will be receiving specific content that will be required to be had on the website.
New desigins are still welcome. Please continue to contact me if you have questions about your individual designs.
Thanks!
Crest Horn

```html
<!DOCTYPE html>
<html lang="en">
<head>
<meta charset="utf-8">
<title>Crest Horn Instruments</title>
<link href="https://fonts.googleapis.com/css2?family=Open+Sans:wght@400;600;700&family=Arimo:wght@400;700&display=swap" rel="stylesheet">
<style>
:root{
  --red:#b01e23;
  --red-dark:#9b0f14;
  --red-soft:#c9474a;
  --panel:#efefef;
  --tile:#f1f1f1;
  --text:#444;
  --dark:#222;
  --white:#fff;
}
*{margin:0;padding:0;box-sizing:border-box}
html,body{width:974px;height:1200px;overflow:hidden;background:var(--white)}
body{position:relative;font-family:"Arimo",Arial,sans-serif;color:var(--text)}
.abs{position:absolute}
.backdrop{left:0;top:0;width:974px;height:500px;
  background:linear-gradient(180deg,rgba(190,60,65,.55) 0%,rgba(205,120,125,.45) 45%,rgba(255,255,255,0) 100%),
  linear-gradient(90deg,#c8b7b7,#e9dede 50%,#c8b7b7)}
.page-white{left:140px;top:370px;width:694px;height:830px;background:var(--white)}
.logo-mark{left:140px;top:17px;width:52px;height:52px;border-radius:50%;background:var(--white)}
.brand{left:201px;top:20px;font-family:"Open Sans",sans-serif;font-weight:700;font-size:21px;line-height:25px;letter-spacing:1.5px;color:var(--red)}
.toolbar{left:594px;top:0;height:29px;display:flex}
.tool{width:31px;height:29px;background:#9d9d9d;border-right:1px solid #b5b5b5;display:flex;align-items:center;justify-content:center}
.tool.active{background:#111}
.tool svg{width:10px;height:10px}
.cart{width:87px;height:29px;background:#a8a8a8;color:#fff;font-size:8px;display:flex;align-items:center;justify-content:center;gap:4px;margin-left:3px}
.phone{right:140px;top:49px;font-family:"Open Sans",sans-serif;font-weight:700;font-size:15px;color:var(--red);display:flex;align-items:center;gap:5px}
.nav{left:140px;top:88px;width:694px;height:37px;background:var(--white)}
.nav-home{left:0;top:0;width:47px;height:37px;background:var(--red-dark);display:flex;align-items:center;justify-content:center}
.nav-item{top:0;line-height:37px;font-family:"Open Sans",sans-serif;font-size:10.5px;color:var(--red);transform:translateX(-50%)}
.slider{left:144px;top:131px;width:686px;height:239px;background:linear-gradient(180deg,#b9a7a5 0%,#c1454a 40%,#8e2a2d 75%,#3a3a3a 100%)}
.slide-caption{left:0;top:171px;width:686px;height:44px;background:linear-gradient(90deg,rgba(0,0,0,0),rgba(0,0,0,.55) 20%,rgba(0,0,0,.55) 80%,rgba(0,0,0,0));color:#fff;font-family:"Open Sans",sans-serif;font-weight:600;font-size:14px;letter-spacing:2px;text-align:center;line-height:30px}
.dots{left:305px;top:223px;display:flex;gap:3px}
.dot{width:8px;height:8px;border-radius:50%;background:#fff}
.dot.on{background:var(--red)}
.arrow{top:110px;width:28px;height:24px;background:rgba(255,255,255,.5);display:flex;align-items:center;justify-content:center}
.arrow.right{background:rgba(255,255,255,.85)}
h2{font-family:"Open Sans",sans-serif;font-weight:600;color:var(--red);font-size:19.5px;line-height:22px}
.intro{left:155px;top:440px;width:434px;font-size:7px;line-height:9px;color:#555}
.intro p{margin-bottom:8px}
.tile{width:132px;height:138px;background:var(--tile)}
.tile .pic{left:22px;top:10px;width:88px;height:95px;border-radius:4px;background:linear-gradient(135deg,#d7d2c6,#8d8a88)}
.tile .pic.brass{background:linear-gradient(135deg,#e6d49a,#b99a3c)}
.tile .pic.sax{background:linear-gradient(135deg,#c9a85a,#3c3f74)}
.tile .pic.wood{background:linear-gradient(135deg,#7b7f86,#1f2226)}
.tile .label{left:0;bottom:6px;width:132px;text-align:center;font-family:"Open Sans",sans-serif;font-size:13px;color:#333}
.tile.feature{height:168px;background:var(--red)}
.tile.feature .pic{background:linear-gradient(135deg,#8c1418,#2a0507);opacity:.8}
.feature-name{left:0;top:73px;width:132px;text-align:center;color:#fff;font-family:"Open Sans",sans-serif;font-size:12px;font-weight:600}
.feature-price{left:0;top:91px;width:132px;text-align:center;color:#fff;font-size:7px}
.tile-btns{left:25px;top:136px;display:flex;gap:3px}
.tbtn{width:27px;height:21px;background:#ddd;display:flex;align-items:center;justify-content:center}
.tbtn.red{background:var(--red-dark)}
.side{left:608px;width:221px;background:var(--panel)}
.side h2{position:absolute;left:7px}
.news{left:0;width:221px;height:50px}
.news.on{background:var(--red-dark);color:#fff}
.news .thumb{left:8px;top:6px;width:60px;height:39px;background:linear-gradient(135deg,#c8a09a,#8b3a3a)}
.news .n-title{left:73px;top:7px;font-size:7.5px;font-weight:700}
.news .n-body{left:73px;top:23px;width:142px;font-size:7px;line-height:9px}
.s-thumb{left:8px;width:60px;height:39px;background:var(--red-soft);display:flex;align-items:center;justify-content:center}
.s-text{left:72px;width:142px;font-size:7px;line-height:9.2px;color:#555}
.social{left:149px;top:1163px;display:flex;gap:5px}
.social span{width:22px;height:22px;border-radius:50%;background:#1d5fa8}
.social span.pink{background:#e97993}
.copyright{right:140px;top:1169px;font-size:8px;color:#222}
</style>
</head>
<body>

<div class="abs backdrop" role="img" aria-label="Faded photo of a marching band in red and white uniforms"></div>
<div class="abs page-white"></div>

<!-- header -->
<div class="abs logo-mark"></div>
<div class="abs brand">CREST HORN<br>INSTRUMENTS</div>

<div class="abs toolbar">
  <div class="tool"><svg viewBox="0 0 10 10"><path d="M5 9 1 5a2 2 0 0 1 4-3 2 2 0 0 1 4 3z" fill="#fff"/></svg></div>
  <div class="tool"><svg viewBox="0 0 10 10"><circle cx="5" cy="3" r="2" fill="#fff"/><rect x="2" y="6" width="6" height="3" fill="#fff"/></svg></div>
  <div class="tool"><svg viewBox="0 0 10 10"><rect x="1" y="2" width="7" height="7" fill="none" stroke="#fff"/><path d="M4 6 9 1" stroke="#fff"/></svg></div>
  <div class="tool"><svg viewBox="0 0 10 10"><rect x="3" y="4" width="4" height="5" fill="none" stroke="#fff"/><path d="M4 4V2h2v2" stroke="#fff" fill="none"/></svg></div>
  <div class="tool active"><svg viewBox="0 0 10 10"><circle cx="2" cy="5" r="1.5" fill="#fff"/><circle cx="8" cy="2" r="1.5" fill="#fff"/><circle cx="8" cy="8" r="1.5" fill="#fff"/><path d="M2 5 8 2M2 5l6 3" stroke="#fff"/></svg></div>
  <div class="cart"><svg width="10" height="9" viewBox="0 0 10 9"><path d="M0 1h2l1 5h6l1-4H3" fill="none" stroke="#fff"/><circle cx="4" cy="8" r="1" fill="#fff"/><circle cx="8" cy="8" r="1" fill="#fff"/></svg>Cart: (empty)</div>
</div>

<div class="abs phone"><svg width="13" height="13" viewBox="0 0 12 12"><path d="M3 1 5 3 4 5q1 2 3 3l2-1 2 2-2 2Q3 10 1 3z" fill="#b01e23"/></svg>10 20 30 40 50</div>

<nav class="abs nav">
  <div class="abs nav-home"><svg width="12" height="11" viewBox="0 0 12 11"><path d="M6 0 0 5h2v6h3V7h2v4h3V5h2z" fill="#fff"/></svg></div>
  <div class="abs nav-item" style="left:138px">INSTRUMENTS</div>
  <div class="abs nav-item" style="left:263px">TRADE IN</div>
  <div class="abs nav-item" style="left:375px">SELL OUT</div>
  <div class="abs nav-item" style="left:477px">LOGIN</div>
  <div class="abs nav-item" style="left:579px">CONTACT</div>
</nav>

<!-- slider -->
<div class="abs slider" role="img" aria-label="Marching band drummers in red uniforms and white plumed hats">
  <div class="abs arrow" style="left:5px"><svg width="10" height="8" viewBox="0 0 10 8"><path d="M10 4H2M5 1 2 4l3 3" stroke="#fff" stroke-width="1.5" fill="none"/></svg></div>
  <div class="abs arrow right" style="left:651px"><svg width="10" height="8" viewBox="0 0 10 8"><path d="M0 4h8M5 1l3 3-3 3" stroke="#b01e23" stroke-width="1.5" fill="none"/></svg></div>
  <div class="abs slide-caption">LARKFIELD MIDDLE SCHOOL</div>
  <div class="abs dots"><span class="dot"></span><span class="dot"></span><span class="dot on"></span><span class="dot"></span><span class="dot"></span><span class="dot"></span><span class="dot"></span></div>
</div>

<!-- welcome -->
<h2 class="abs" style="left:154px;top:402px">Welcome To Crest Horn Instruments</h2>
<div class="abs intro">
  <p>We show you financial benefits of buying used band instruments for junior high students.This would be opposed to the current and costly option of renting cheap quality instruments from the 2 or 3 local music stores that charge a monthly fee that over the years charges the buyer 3 or 4x over..</p>
  <p>Ut wisi enim ad minim veniam, quis nostrud exerci tation ullamcorper suscipit lobortis nisl ut aliquip ex ea commodo consequat. Duis autem vel eum iriure dolor in hendrerit in vulputate velit esse molestie consequat, vel illum dolore eu feugiat nulla facilisis at vero eros et accumsan et iusto odio dignissim qui blandit praesent luptatum zzril delenit augue duis dolore te feugait nulla facilisi.</p>
  <p>Scipit lobortis nisl ut aliquip ex ea commodo consequat. Duis autem vel eum iriure dolor in hendrerit in vulputate velit esse molestie consequat, vel illum dolore eu feugiat nulla facilisis at vero eros et accumsan et iusto odio dignissim qui blandit praesent luptatum zzril delenit augue duis dolore te feugait nulla facilisi.</p>
</div>

<!-- products -->
<h2 class="abs" style="left:154px;top:557px">Latest Products</h2>

<div class="abs tile feature" style="left:155px;top:590px">
  <div class="abs pic" role="img" aria-label="Flute product photo"></div>
  <svg class="abs" style="left:57px;top:52px" width="18" height="18" viewBox="0 0 18 18"><circle cx="7" cy="7" r="5.5" fill="none" stroke="#fff" stroke-width="2"/><path d="M11 11l5 5M7 4v6M4 7h6" stroke="#fff" stroke-width="2"/></svg>
  <div class="abs feature-name">FLUTE</div>
  <div class="abs feature-price">$50.00</div>
  <div class="abs tile-btns">
    <div class="tbtn"><svg width="10" height="9" viewBox="0 0 10 9"><path d="M0 1h2l1 5h6l1-4H3" fill="none" stroke="#999"/></svg></div>
    <div class="tbtn"><svg width="11" height="7" viewBox="0 0 11 7"><path d="M0 3.5Q5.5-2 11 3.5 5.5 9 0 3.5z" fill="none" stroke="#999"/><circle cx="5.5" cy="3.5" r="1.5" fill="#999"/></svg></div>
    <div class="tbtn red"><svg width="11" height="11" viewBox="0 0 12 12"><path d="M6 1l1.5 3.3 3.5.4-2.6 2.4.7 3.5L6 8.8 2.9 10.6l.7-3.5L1 4.7l3.5-.4z" fill="none" stroke="#fff"/></svg></div>
  </div>
</div>
<div class="abs tile" style="left:308px;top:590px"><div class="abs pic wood" role="img" aria-label="Clarinet product photo"></div><div class="abs label">Clarinet</div></div>
<div class="abs tile" style="left:461px;top:590px"><div class="abs pic brass" role="img" aria-label="Trombone product photo"></div><div class="abs label">Trombone</div></div>

<div class="abs tile" style="left:155px;top:774px"><div class="abs pic sax" role="img" aria-label="Alto sax product photo"></div><div class="abs label">Alto Sax</div></div>
<div class="abs tile" style="left:308px;top:774px"><div class="abs pic brass" role="img" aria-label="Trumpet product photo"></div><div class="abs label">Trumpet</div></div>
<div class="abs tile" style="left:461px;top:774px"><div class="abs pic wood" role="img" aria-label="Clarinet product photo"></div><div class="abs label">Clarinet</div></div>

<div class="abs tile" style="left:155px;top:953px"><div class="abs pic sax" role="img" aria-label="Alto sax product photo"></div><div class="abs label">Alto Sax</div></div>
<div class="abs tile" style="left:308px;top:953px"><div class="abs pic brass" role="img" aria-label="Trumpet product photo"></div><div class="abs label">Trumpet</div></div>
<div class="abs tile" style="left:461px;top:953px"><div class="abs pic wood" role="img" aria-label="Clarinet product photo"></div><div class="abs label">Clarinet</div></div>

<!-- sidebar -->
<aside class="abs side" style="top:386px;height:152px">
  <h2 style="top:13px">Latest News</h2>
  <div class="abs news on" style="top:42px">
    <div class="abs thumb" role="img" aria-label="News photo of a band performance"></div>
    <div class="abs n-title">Lorem Ipsum Dolor</div>
    <div class="abs n-body">Ut wisi enim ad minim veniam, quis nostrud exerci tation ullamcorper ....</div>
  </div>
  <div class="abs news" style="top:93px">
    <div class="abs thumb" role="img" aria-label="News photo of a parade"></div>
    <div class="abs n-title" style="color:#444">Lorem Ipsum Dolor</div>
    <div class="abs n-body">Ut wisi enim ad minim veniam, quis nostrud exerci tation ullamcorper ....</div>
  </div>
</aside>

<aside class="abs side" style="top:542px;height:132px">
  <h2 style="top:14px">Rent-to-Own<br>Musical Instruments</h2>
  <div class="abs s-thumb" style="top:72px" role="img" aria-label="Instrument thumbnail"><svg width="11" height="11" viewBox="0 0 18 18"><circle cx="7" cy="7" r="5.5" fill="none" stroke="#fff" stroke-width="2.5"/><path d="M11 11l5 5" stroke="#fff" stroke-width="2.5"/></svg></div>
  <div class="abs s-text" style="top:72px">Rent to own your own musical instrument in the San Jose area! All rental payments apply to the purchase.<br><br>Check Rent to Own for more info!</div>
</aside>

<aside class="abs side" style="top:679px;height:152px">
  <h2 style="top:15px">Music Lessons in San<br>Jose</h2>
  <div class="abs s-thumb" style="top:68px" role="img" aria-label="Instrument thumbnail"><svg width="11" height="11" viewBox="0 0 18 18"><circle cx="7" cy="7" r="5.5" fill="none" stroke="#fff" stroke-width="2.5"/><path d="M11 11l5 5" stroke="#fff" stroke-width="2.5"/></svg></div>
  <div class="abs s-text" style="top:68px">We have music lessons for students of all ages. Harmony Hall offers music lessons for all the major instruments like clarinet, trumpet, saxophone, flute violin, piano, guitar, bass, voice, and drums. Come learn an instrument with our experienced music teachers!</div>
</aside>

<aside class="abs side" style="top:837px;height:152px">
  <h2 style="top:14px">Musical Instrument<br>Repairs</h2>
  <div class="abs s-thumb" style="top:66px" role="img" aria-label="Instrument thumbnail"><svg width="11" height="11" viewBox="0 0 18 18"><circle cx="7" cy="7" r="5.5" fill="none" stroke="#fff" stroke-width="2.5"/><path d="M11 11l5 5" stroke="#fff" stroke-width="2.5"/></svg></div>
  <div class="abs s-text" style="top:66px">Highly experienced musical instrument repair professionals will repair your string, woodwind and brass instruments. In house repairs, walk-ins welcome. Our staff will also remove dents, tune and restring instruments.</div>
</aside>

<aside class="abs side" style="top:994px;height:138px">
  <h2 style="top:14px">Music Teacher<br>Profile</h2>
  <div class="abs s-thumb" style="top:67px"><svg width="11" height="11" viewBox="0 0 18 18"><circle cx="7" cy="7" r="5.5" fill="none" stroke="#fff" stroke-width="2.5"/><path d="M11 11l5 5" stroke="#fff" stroke-width="2.5"/></svg></div>
  <div class="abs s-text" style="top:67px">Highly experienced music teacher professionals will teach you string, woodwind and brass instruments. In house repairs, walk-ins welcome. Our staff will also remove dents, tune and restring instruments.</div>
</aside>

<!-- footer -->
<div class="abs social"><span></span><span></span><span></span><span class="pink"></span></div>
<div class="abs copyright">Copyright © 2014 CREST HORN INSTRUMENTS. All Rights Reserved.</div>

</body>
</html>
```